UK landscaping company needs website

We, Brackwell Landscapes need a website design for a company based in Surrey, UK. The design should be bold and playful. We have three main areas of work driveways, paving and fencing. It shouldn't be too heavy in text and concentrate on the pictures from previous jobs we've completed. You may use stock images for the design, these can be changed if you are successful. Please don’t just copy the flyer it is just there to provide content.
We have a logo design which we would also like editing slightly.
Here are some of my local competitors
https://www.pelmarlandscapes.example.co.uk/

https://www.twinfirgardendesign.example.com/

https://kestbyrnlandscapes.example.co.uk/

Industry/Entity Type

Landscaping

Coding

Coded - Design and coding required

Number of Pages Required

3 page

Font styles to use
Sans Serif

Requirements
Must have
• Pictures of my previous jobs.
Must be mobile friendly
Easy to navigate
Nice to have
• Try to use different colours. It would be good to have some designs that aren’t just black and green.
I’d like some curves in the design.
Should not have
• We install hard landscaping. Think more building/construction and less plants and cutting grass.

```html
<!DOCTYPE html>
<html lang="en">
<head>
<meta charset="utf-8">
<title>Brackwell Landscapes – Our Services</title>
<link rel="stylesheet" href="https://fonts.googleapis.com/css2?family=Roboto:wght@400;500;700;900&family=Rubik:wght@400;500&display=swap">
<style>
:root{
  --green:#5dbb2e;
  --green-dark:#4a9a22;
  --ink:#222222;
  --navy:#2a3350;
  --muted:#7c8294;
  --grey-band:#ececec;
  --dark:#2b2b2b;
  --white:#ffffff;
  --head:"Roboto",sans-serif;
  --body:"Rubik",sans-serif;
}
*{box-sizing:border-box;margin:0;padding:0}
html,body{width:1200px;height:3421px;overflow:hidden;background:var(--white)}
.page{position:relative;width:1200px;height:3421px;overflow:hidden;font-family:var(--body);color:var(--ink)}

/* header */
.site-header{position:absolute;left:0;top:0;width:1200px;height:70px;background:var(--dark);z-index:5}
.brand{position:absolute;left:130px;top:24px;color:var(--white);font:700 22px/1 var(--head);letter-spacing:.5px;display:flex;align-items:center;gap:8px;white-space:nowrap}
.brand .dot{width:12px;height:12px;border-radius:50%;background:var(--green)}
.main-nav a{position:absolute;top:27px;color:var(--white);font:500 16px/1 var(--head);text-decoration:none;white-space:nowrap}
.main-nav a.active{color:var(--green);text-decoration:underline;text-underline-offset:4px}
.estimate{position:absolute;left:998px;top:0;width:202px;height:70px;background:var(--green);color:var(--white);padding:14px 0 0 28px;font-family:var(--head)}
.estimate small{display:block;font:700 14px/1 var(--head)}
.estimate strong{display:block;font:700 22px/1.1 var(--head);margin-top:3px;white-space:nowrap}

/* hero */
.hero-photo{position:absolute;left:0;top:70px;width:1200px;height:600px;background:linear-gradient(100deg,#6a4528 0%,#8a5e38 35%,#9b7550 55%,#7e8a5a 75%,#6fa83a 100%)}
.hero-title{position:absolute;left:0;top:196px;width:1200px;text-align:center;color:var(--white);font:700 56px/1.1 var(--head)}
.hero-sub{position:absolute;left:360px;top:274px;width:480px;text-align:center;color:var(--white);font:400 18px/1.35 var(--body)}
.hero-curve{position:absolute;left:0;top:420px}

/* intro */
.intro-title{position:absolute;left:0;top:612px;width:1200px;text-align:center;font:900 45px/1 var(--head);color:var(--ink)}
.intro-title span{color:var(--green)}
.intro-text{position:absolute;left:266px;top:674px;width:668px;text-align:center;font:400 14px/24px var(--body);color:#333}

/* services */
.band{position:absolute;left:0;width:1200px}
.band.grey{background:var(--grey-band)}
.photo-ring{position:absolute;width:356px;height:356px;border-radius:50%;background:var(--green);padding:24px}
.photo-ring .inner{width:100%;height:100%;border-radius:50%;background:var(--white);padding:6px}
.photo-ring .photo{width:100%;height:100%;border-radius:50%}
.service{position:absolute;width:380px}
.service h2{font:700 37px/1 var(--head);color:var(--ink);margin-bottom:30px}
.point{position:relative;padding-left:33px;margin-bottom:26px}
.point svg{position:absolute;left:8px;top:3px}
.point h3{font:500 15px/1.2 var(--body);color:var(--navy);margin-bottom:9px}
.point p{font:400 14px/21px var(--body);color:var(--muted)}

/* explore */
.kicker{position:absolute;left:0;top:2376px;width:1232px;text-align:center;font:500 10px/1 var(--head);color:#333}
.explore-title{position:absolute;left:0;top:2406px;width:1232px;text-align:center;font:500 29px/1 var(--head);color:var(--ink)}
.feature{position:absolute;top:2505px;width:300px}
.feature svg{position:absolute;left:0;top:0}
.feature h4{position:absolute;left:73px;top:4px;font:500 17px/1 var(--head);color:var(--ink);white-space:nowrap}
.feature p{position:absolute;left:73px;top:38px;width:225px;font:400 13px/24px var(--head);color:#555}

/* cta */
.cta-photo{position:absolute;left:0;top:2660px;width:1200px;height:408px;background:linear-gradient(180deg,#4e9a26 0%,#6cc23d 55%,#7ccc4e 100%)}
.cta-curve{position:absolute;left:0;top:2650px}
.cta-title{position:absolute;left:0;top:2840px;width:1200px;text-align:center;color:var(--white);font:900 32px/42px var(--head);letter-spacing:-.5px}
.cta-btn{position:absolute;left:479px;top:2939px;width:242px;height:46px;background:var(--dark);color:var(--white);font:500 17px/46px var(--body);text-align:center;border-radius:3px;text-decoration:none;white-space:nowrap}
.cta-btn svg{vertical-align:-3px;margin-left:8px}

/* footer */
.site-footer{position:absolute;left:0;top:3067px;width:1200px;height:354px;background:var(--dark);color:var(--white)}
.footer-brand{position:absolute;left:133px;top:86px;width:220px;display:flex;align-items:center;gap:12px}
.footer-brand span.name{font:700 27px/30px var(--head);letter-spacing:.5px}
.footer-brand .dot{width:14px;height:14px;border-radius:50%;background:var(--green);flex:none}
.fcol{position:absolute;top:78px;font-family:var(--head)}
.fcol a{display:block;color:var(--white);text-decoration:none;white-space:nowrap}
.fcol.main a{font:500 15px/35px var(--head)}
.fcol h5{font:500 15px/1 var(--head);margin-bottom:14px;white-space:nowrap}
.fcol.sub a{font:400 13px/27px var(--head);text-decoration:underline}
.footer-map{position:absolute;left:786px;top:73px;width:282px;height:112px;background:linear-gradient(135deg,#dfe6ee,#cdd8e3 60%,#e8e1c9);border-bottom:3px solid #e6b84a}
.social{position:absolute;top:230px;width:32px;height:32px;border:1.5px solid #cfcfcf;border-radius:50%}
.footer-rule{position:absolute;left:26px;top:288px;width:1148px;height:1px;background:#555}
.copyright{position:absolute;left:0;top:309px;width:1200px;text-align:center;font:400 14px/1 var(--body);color:#ddd}
</style>
</head>
<body>
<div class="page">

  <header class="site-header">
    <div class="brand"><span>BRACKWELL LANDSCAPES</span><span class="dot"></span></div>
    <nav class="main-nav">
      <a href="#" style="left:475px">HOME</a>
      <a href="#" style="left:564px">SERVICES</a>
      <a href="#" class="active" style="left:679px">ABOUT</a>
      <a href="#" style="left:774px">OUR WORK</a>
      <a href="#" style="left:899px">CONTACT</a>
    </nav>
    <div class="estimate"><small>FREE ESTIMATES</small><strong>07700 900481</strong></div>
  </header>

  <div class="hero-photo" role="img" aria-label="Timber fence beside a gravel border and fresh lawn"></div>
  <h1 class="hero-title">Our Services</h1>
  <p class="hero-sub">Lorem Ipsum is simply dummy text of the printing and typesetting industry.</p>
  <svg class="hero-curve" width="1200" height="260" viewBox="0 0 1200 260" aria-hidden="true">
    <path d="M0 246 Q600 10 1200 92 L1200 260 L0 260 Z" fill="#ffffff"/>
    <path d="M0 226 Q600 -36 1200 68 L1200 94 Q600 8 0 250 Z" fill="#5dbb2e"/>
  </svg>

  <h2 class="intro-title">OUR <span>SERVICES</span></h2>
  <p class="intro-text">Brackwell Landscapes are a professional and experienced landscaping business that delivers stunning results in all aspects of driveway and garden construction. We work throughout Surrey and surrounding areas. We pride ourselves on excellent workmanship and attention to detail. We use only top quality materials to ensure an outstanding and long-lasting finish, installed using both traditional and modern techniques.</p>

  <!-- driveways -->
  <section class="band grey" style="top:869px;height:470px"></section>
  <div class="photo-ring" style="left:211px;top:923px"><div class="inner"><div class="photo" role="img" aria-label="Block-paved driveway with gravel edging" style="background:linear-gradient(160deg,#8d8a85,#5e6066 60%,#b9b6ae)"></div></div></div>
  <div class="service" style="left:645px;top:976px">
    <h2>DRIVEWAYS</h2>
    <div class="point"><svg width="12" height="10" viewBox="0 0 12 10"><path d="M1 5l3.5 3.5L11 1" fill="none" stroke="#5dbb2e" stroke-width="1.6"/></svg><h3>Lorem Ipsum is simply dummy</h3><p>Lorem Ipsum is simply dummy text of the printing and typesetting industry.</p></div>
    <div class="point"><svg width="12" height="10" viewBox="0 0 12 10"><path d="M1 5l3.5 3.5L11 1" fill="none" stroke="#5dbb2e" stroke-width="1.6"/></svg><h3>Lorem Ipsum is simply dummy</h3><p>Lorem Ipsum is simply dummy text of the printing and typesetting industry.</p></div>
  </div>

  <!-- paving -->
  <div class="service" style="left:186px;top:1446px">
    <h2>PAVING</h2>
    <div class="point"><svg width="12" height="10" viewBox="0 0 12 10"><path d="M1 5l3.5 3.5L11 1" fill="none" stroke="#5dbb2e" stroke-width="1.6"/></svg><h3>Lorem Ipsum is simply dummy</h3><p>Lorem Ipsum is simply dummy text of the printing and typesetting industry.</p></div>
    <div class="point"><svg width="12" height="10" viewBox="0 0 12 10"><path d="M1 5l3.5 3.5L11 1" fill="none" stroke="#5dbb2e" stroke-width="1.6"/></svg><h3>Lorem Ipsum is simply dummy</h3><p>Lorem Ipsum is simply dummy text of the printing and typesetting industry.</p></div>
  </div>
  <div class="photo-ring" style="left:631px;top:1400px"><div class="inner"><div class="photo" role="img" aria-label="Sandstone patio with circular paving feature" style="background:linear-gradient(170deg,#9aa08c,#a58c82 45%,#8f7a72)"></div></div></div>

  <!-- fencing -->
  <section class="band grey" style="top:1829px;height:469px"></section>
  <div class="photo-ring" style="left:211px;top:1884px"><div class="inner"><div class="photo" role="img" aria-label="New timber fence with gravel border and lawn" style="background:linear-gradient(160deg,#7d8b8c,#9a6e42 40%,#b08457 65%,#6aa83a)"></div></div></div>
  <div class="service" style="left:645px;top:1935px">
    <h2>FENCING</h2>
    <div class="point"><svg width="12" height="10" viewBox="0 0 12 10"><path d="M1 5l3.5 3.5L11 1" fill="none" stroke="#5dbb2e" stroke-width="1.6"/></svg><h3>Lorem Ipsum is simply dummy</h3><p>Lorem Ipsum is simply dummy text of the printing and typesetting industry.</p></div>
    <div class="point"><svg width="12" height="10" viewBox="0 0 12 10"><path d="M1 5l3.5 3.5L11 1" fill="none" stroke="#5dbb2e" stroke-width="1.6"/></svg><h3>Lorem Ipsum is simply dummy</h3><p>Lorem Ipsum is simply dummy text of the printing and typesetting industry.</p></div>
  </div>

  <!-- explore -->
  <p class="kicker">THE BEST OF A KIND</p>
  <h2 class="explore-title">EXPLORE OUR COMPANY</h2>
  <div class="feature" style="left:146px">
    <svg width="48" height="48" viewBox="0 0 48 48" fill="none" stroke="#222" stroke-width="2"><circle cx="24" cy="26" r="16"/><path d="M24 16v10h8M8 12l6-6M40 12l-6-6M13 40l-4 5M35 40l4 5"/></svg>
    <h4>Dedicated Team</h4>
    <p>Objectively innovate empowered manufactured products whereas parallel platforms.</p>
  </div>
  <div class="feature" style="left:467px">
    <svg width="48" height="48" viewBox="0 0 48 48" fill="none" stroke="#222" stroke-width="2"><path d="M12 36V22a12 12 0 0 1 24 0v14l4 4H8z"/><path d="M20 44a4 4 0 0 0 8 0M24 6v4"/></svg>
    <h4>Best Engineers</h4>
    <p>Distinctively re-engineer revolutionary meta-services and premium architectures.</p>
  </div>
  <div class="feature" style="left:787px">
    <svg width="48" height="48" viewBox="0 0 48 48" fill="none" stroke="#222" stroke-width="2"><circle cx="34" cy="13" r="9"/><path d="M27 19L8 36l4 4 18-18M8 36c-3 3-4 6-2 8"/></svg>
    <h4>24/7 Supports</h4>
    <p>Holisticly predominate extensible testing procedures for reliable supply chains.</p>
  </div>

  <!-- call to action -->
  <div class="cta-photo" role="img" aria-label="Paved garden with timber posts under a green tint"></div>
  <svg class="cta-curve" width="1200" height="260" viewBox="0 0 1200 260" aria-hidden="true">
    <path d="M0 0 L1200 0 L1200 64 Q600 -44 0 246 Z" fill="#ffffff"/>
    <path d="M0 246 Q600 -44 1200 64" fill="none" stroke="#6cc23d" stroke-width="8"/>
  </svg>
  <h2 class="cta-title">YOUR GARDEN AND DRIVEWAY CARED FOR<br>THE WAY THEY SHOULD BE</h2>
  <a class="cta-btn" href="#">START MY ESTIMATE<svg width="17" height="17" viewBox="0 0 17 17"><circle cx="8.5" cy="8.5" r="8" fill="#fff"/><path d="M7 5l3.5 3.5L7 12" fill="none" stroke="#2b2b2b" stroke-width="1.8"/></svg></a>

  <footer class="site-footer">
    <div class="footer-brand"><span class="name">BRACKWELL<br>LANDSCAPES</span><span class="dot"></span></div>
    <nav class="fcol main" style="left:385px;top:62px">
      <a href="#">HOME</a><a href="#">ABOUT US</a><a href="#">OUR WORK</a><a href="#">CONTACT</a>
    </nav>
    <div class="fcol sub" style="left:505px">
      <h5>SERVICES</h5><a href="#">Driveways</a><a href="#">Paving</a><a href="#">Fencing</a>
    </div>
    <div class="fcol sub" style="left:633px">
      <h5>QUICK LINKS</h5><a href="#">FAQ</a><a href="#">Testimonials</a><a href="#">Sitemap</a>
    </div>
    <div class="footer-map" role="img" aria-label="Map showing the business location"></div>
    <span class="social" style="left:525px" aria-label="Social profile"></span>
    <span class="social" style="left:564px" aria-label="Social profile"></span>
    <span class="social" style="left:602px" aria-label="Social profile"></span>
    <span class="social" style="left:642px" aria-label="Social profile"></span>
    <div class="footer-rule"></div>
    <p class="copyright">© 2020 Brackwell Landscapes. All Rights are Reserved.</p>
  </footer>

</div>
</body>
</html>
```